Create a proposal + product powerpoint

Please see the powerpoint for the slides. There are about 20 slides to be created. Rest of them are for reference and show the design that I like.

I would like to move fast on this, since I need to present it next week (in the week of April 21st).

Please download the current content from here:
https://www.parcelbrook.net/fetch/qRtVmXzLwPkNbYcD

Please make at least 4 slides with the specific content so I can assess your design style.

Target Market(s)

Business Audience and very senior technical audience
Decision Makers

Industry/Entity Type

Product

Colors
e34297
a64599

Requirements
Must have
• Should be very clean, crisp.

I like to use Icons as shown in the powerpoint.... Please see the appendix of the slide deck that shows the various icons. Most of them just have plain text, and I would like to organize so that it does not look like some is just reading text.

I would like to focus on the design aspects so that the audience is clear on how the solution works.

Every page should some graphic element based on the slides shown in the appendix.

```html
<!DOCTYPE html>
<html lang="en">
<head>
<meta charset="utf-8">
<title>Lifecycle Management Solution</title>
<link rel="stylesheet" href="https://fonts.googleapis.com/css2?family=Play:wght@400;700&family=Saira+Semi+Condensed:wght@400;500;600&display=swap">
<style>
  :root {
    --pink: #e34297;
    --purple: #a64599;
    --ink: #3b383d;
    --paper: #ffffff;
    --mist: #f6ebf5;
    --haze: #ead3ea;
    --sky: #dfe4f3;
  }
  * { margin: 0; padding: 0; box-sizing: border-box; }
  html, body { width: 1200px; height: 900px; overflow: hidden; background: var(--paper); }
  .slide {
    position: relative;
    width: 1200px;
    height: 900px;
    overflow: hidden;
    background: var(--paper);
    font-family: "Play", sans-serif;
  }
  .backdrop {
    position: absolute;
    inset: 0;
    background:
      radial-gradient(ellipse 520px 360px at 960px 640px, var(--haze) 0%, rgba(234,211,234,0) 70%),
      radial-gradient(ellipse 700px 160px at 560px 700px, var(--sky) 0%, rgba(223,228,243,0) 70%),
      linear-gradient(180deg, rgba(246,235,245,0) 0%, rgba(246,235,245,0.5) 45%, var(--mist) 100%);
  }
  .title-bar {
    position: absolute;
    left: 0; top: 33px;
    width: 15px; height: 63px;
    background: var(--purple);
  }
  .slide-title {
    position: absolute;
    left: 28px; top: 36px;
    font-family: "Saira Semi Condensed", sans-serif;
    font-weight: 400;
    font-size: 42px;
    line-height: 1.2;
    color: var(--pink);
  }
  .brand-name {
    position: absolute;
    right: 45px; top: 50px;
    font-family: "Saira Semi Condensed", sans-serif;
    font-weight: 600;
    font-size: 39px;
    line-height: 1.2;
    color: var(--purple);
  }
  .section-title {
    position: absolute;
    left: 30px; top: 200px;
    font-family: "Saira Semi Condensed", sans-serif;
    font-weight: 500;
    font-size: 38px;
    line-height: 1.2;
    color: var(--purple);
  }
  .feature-list {
    position: absolute;
    left: 35px; top: 288px;
    list-style: none;
  }
  .feature-list li {
    display: flex;
    align-items: center;
    height: 79.5px;
    font-size: 36px;
    color: var(--ink);
  }
  .feature-list svg { width: 38px; height: 38px; margin-right: 24px; flex: none; }
  .copyright {
    position: absolute;
    right: 33px; top: 840px;
    font-family: "Saira Semi Condensed", sans-serif;
    font-size: 21px;
    color: var(--purple);
  }
</style>
</head>
<body>
<main class="slide">
  <div class="backdrop" role="img" aria-label="Soft flowing violet wave lines across the lower half of the slide"></div>

  <div class="title-bar"></div>
  <h1 class="slide-title">Lifecycle Management Solution</h1>
  <div class="brand-name">LOGO HERE</div>

  <h2 class="section-title">SUB Text title here</h2>

  <ul class="feature-list">
    <li><svg viewBox="0 0 38 38" aria-hidden="true"><rect x="1" y="1" width="36" height="36" rx="15" fill="var(--purple)"/><path d="M15 11 L23 19 L15 27" fill="none" stroke="#fff" stroke-width="4.5" stroke-linecap="round" stroke-linejoin="round"/></svg>Code promotion</li>
    <li><svg viewBox="0 0 38 38" aria-hidden="true"><rect x="1" y="1" width="36" height="36" rx="15" fill="var(--purple)"/><path d="M15 11 L23 19 L15 27" fill="none" stroke="#fff" stroke-width="4.5" stroke-linecap="round" stroke-linejoin="round"/></svg>Change Management</li>
    <li><svg viewBox="0 0 38 38" aria-hidden="true"><rect x="1" y="1" width="36" height="36" rx="15" fill="var(--purple)"/><path d="M15 11 L23 19 L15 27" fill="none" stroke="#fff" stroke-width="4.5" stroke-linecap="round" stroke-linejoin="round"/></svg>Troubleshooting</li>
    <li><svg viewBox="0 0 38 38" aria-hidden="true"><rect x="1" y="1" width="36" height="36" rx="15" fill="var(--purple)"/><path d="M15 11 L23 19 L15 27" fill="none" stroke="#fff" stroke-width="4.5" stroke-linecap="round" stroke-linejoin="round"/></svg>Build and test automation</li>
    <li><svg viewBox="0 0 38 38" aria-hidden="true"><rect x="1" y="1" width="36" height="36" rx="15" fill="var(--purple)"/><path d="M15 11 L23 19 L15 27" fill="none" stroke="#fff" stroke-width="4.5" stroke-linecap="round" stroke-linejoin="round"/></svg>Audit Analysis</li>
  </ul>

  <p class="copyright">Copyright text here</p>
</main>
</body>
</html>
```